Stationary Set Rebrand for Brennick

We are a Canadian Distribution and Service Company that was established in 1969. Over the past 5 decades we have expanded our business and have warehouses across Canada. We specialize in adhesive tapes, adhesives, films, safety, warehouse, shipping, janitorial and packaging supplies.

We have updated our logo design and would like a new corporate branding identity that includes a new fresh Stationary Set (Business Cards, Letterhead, Letterhead MS Word, Envelope, Presentation Folders, Email Signatures, Notepad Covers, etc.)

Target Market(s)

Industrial Business Sector

Font styles to use
Sans Serif

Colors
0054AA
0677BA
7BADD7
CADEEF
E8F1F8
0094D4
00A9DD
6FCCEA
C7EBF8
E9F6FB
00AB8E
00BBA5
67D7C9
C6EFE9
E9F9F6
EB3D1F
EC4F4E
F09395
F8D3D4
FCEDEE

Requirements
Should not have
• Colors not too light, darker colours preferred

```html
<!DOCTYPE html>
<html lang="en">
<head>
<meta charset="utf-8">
<title>Brennick Stationery Set</title>
<link rel="stylesheet" href="https://fonts.googleapis.com/css2?family=Montserrat:wght@400;500;700;800;900&family=Open+Sans:wght@400;600;700&display=swap">
<style>
  :root {
    --red: #e01b2b;
    --red-deep: #c3161f;
    --ink: #111111;
    --paper: #ffffff;
    --stage: #dde1e3;
    --folder-grey: #d4d5d7;
    --text: #1c1c1c;
  }
  * { box-sizing: border-box; margin: 0; padding: 0; }
  html, body { width: 1200px; height: 684px; overflow: hidden; }
  body { background: var(--stage); font-family: "Open Sans", sans-serif; color: var(--text); position: relative; }
  .piece { position: absolute; background: var(--paper); box-shadow: 0 2px 6px rgba(0,0,0,.12); overflow: hidden; }
  .wordmark { font-family: "Montserrat", sans-serif; font-weight: 900; color: var(--ink); letter-spacing: -0.02em; line-height: 1; white-space: nowrap; }
  .band { position: absolute; left: 0; right: 0; display: flex; }
  .band .band-red { background: var(--red); flex: 0 0 46%; }
  .band .band-black { background: var(--ink); flex: 1; }
  .contact-line { display: flex; align-items: center; gap: 3px; white-space: nowrap; }
  .icon { flex: none; }
  .contact { font-family: "Montserrat", sans-serif; }

  /* Envelope front */
  .envelope-front { left: 50px; top: 53px; width: 271px; height: 120px; }
  .envelope-front .wordmark { position: absolute; right: 12px; top: 10px; font-size: 20px; }
  .envelope-front .contact { position: absolute; left: 197px; top: 64px; font-size: 5.3px; line-height: 6.4px; }
  .envelope-front .contact .gap { height: 5px; }
  .envelope-front .band { top: 105px; height: 6px; }

  /* Envelope back */
  .envelope-back { left: 50px; top: 187px; width: 271px; height: 119px; }
  .envelope-back .flap { position: absolute; left: 0; right: 0; top: 0; height: 41px; background: var(--red); border-radius: 0 0 12px 12px; }

  /* Business card front */
  .card-front { left: 51px; top: 317px; width: 264px; height: 150px; border-radius: 18px; background: var(--red); display: flex; align-items: center; justify-content: center; }
  .card-front .wordmark { color: var(--paper); font-size: 40px; }

  /* Business card back & email signature share a layout */
  .contact-card { left: 51px; top: 483px; width: 264px; height: 151px; border-radius: 18px; }
  .contact-card .wordmark { position: absolute; left: 12px; top: 66px; font-size: 23px; }
  .contact-card .divider { position: absolute; left: 132px; top: 29px; width: 1px; height: 95px; background: var(--red); }
  .contact-card .details { position: absolute; left: 152px; top: 30px; font-size: 7.5px; line-height: 9.6px; }
  .contact-card .band { top: 134px; height: 9px; }

  .email-signature { left: 354px; top: 526px; width: 318px; height: 106px; }
  .email-signature .wordmark { position: absolute; left: 24px; top: 36px; font-size: 25px; }
  .email-signature .divider { position: absolute; left: 159px; top: 15px; width: 1px; height: 80px; background: var(--red); }
  .email-signature .details { position: absolute; left: 186px; top: 12px; font-size: 6.6px; line-height: 8.2px; }
  .email-signature .band { top: 96px; height: 5px; }

  .person-name { font-family: "Montserrat", sans-serif; font-size: 15px; line-height: 16px; font-weight: 400; color: var(--ink); }
  .person-name .first { color: var(--red); font-weight: 500; }
  .email-signature .person-name { font-size: 13px; line-height: 13px; }
  .person-title { font-weight: 500; margin-bottom: 5px; }
  .details .block { margin-bottom: 5px; }

  /* Letterhead */
  .letterhead { left: 354px; top: 55px; width: 318px; height: 449px; }
  .letterhead .wordmark { position: absolute; left: 17px; top: 24px; font-size: 30px; }
  .letterhead .head-contact { position: absolute; right: 18px; top: 17px; text-align: right; font-size: 7px; line-height: 8.5px; }
  .letterhead .head-contact .contact-line { justify-content: flex-end; }
  .letterhead .head-contact .gap { height: 4px; }
  .letterhead .rule-black { position: absolute; left: 17px; top: 68px; width: 185px; height: 0.6px; background: var(--ink); }
  .letterhead .rule-red { position: absolute; left: 198px; top: 67px; width: 103px; height: 2px; background: var(--red); }
  .letter-body { position: absolute; left: 17px; top: 108px; width: 284px; font-size: 5.9px; line-height: 8.3px; }
  .letter-body .date { margin-bottom: 6px; }
  .letter-body .recipient { font-weight: 700; font-size: 8px; line-height: 9px; }
  .letter-body .addr { margin: 5px 0 11px; }
  .letter-body .salutation { font-weight: 700; font-size: 8px; line-height: 9px; margin-bottom: 5px; }
  .letter-body p.copy { text-align: justify; margin-bottom: 8px; }
  .signature { position: absolute; left: 17px; top: 332px; width: 86px; height: 20px; background: linear-gradient(90deg, #e9e9e9, #f5f5f5); border-radius: 3px; }
  .signer { position: absolute; left: 17px; top: 353px; }
  .signer .name { font-weight: 700; font-size: 14px; line-height: 15px; color: var(--ink); }
  .signer .role { font-size: 6px; }
  .letterhead .band { top: 428px; height: 8px; }

  /* Presentation folder */
  .folder-front { left: 696px; top: 53px; width: 139px; height: 272px; background: linear-gradient(135deg, #ededee 0%, #cfcfd1 100%); }
  .folder-front .band { top: 247px; height: 6px; }
  .folder-front .wordmark { position: absolute; right: 5px; top: 232px; font-size: 14px; }
  .folder-inside { left: 909px; top: 69px; width: 262px; height: 242px; background: linear-gradient(90deg, #f7f7f7 0%, #e4e4e5 50%, #cbcbcd 50.5%, #d9d9db 100%); }
  .folder-inside .pocket { position: absolute; left: 131px; right: 0; bottom: 0; height: 82px; background: var(--red); border-top-left-radius: 58px 70px; }

  /* Notepad cover */
  .notepad { left: 760px; top: 362px; width: 400px; height: 276px; }
  .notepad .binding { position: absolute; left: 0; right: 0; top: 0; height: 14px; background: #e9e9ea; display: flex; justify-content: space-around; align-items: center; padding: 0 10px; }
  .notepad .ring { width: 6px; height: 10px; border: 2px solid #3a3a3a; border-radius: 3px; }
  .notepad .band { top: 246px; height: 7px; }
  .notepad .wordmark { position: absolute; right: 18px; top: 216px; font-size: 24px; }
</style>
</head>
<body>

<svg width="0" height="0" style="position:absolute">
  <defs>
    <symbol id="icon-phone" viewBox="0 0 10 10"><path d="M2.2 1h1.6l.8 2-1 .8a5 5 0 0 0 2.6 2.6l.8-1 2 .8v1.6c0 .5-.4.9-.9.9A7.8 7.8 0 0 1 1.3 1.9c0-.5.4-.9.9-.9z" fill="#e01b2b"/></symbol>
    <symbol id="icon-mail" viewBox="0 0 10 10"><rect x="1" y="2.2" width="8" height="5.6" rx=".8" fill="#e01b2b"/><path d="M1.4 2.8 5 5.4l3.6-2.6" stroke="#fff" stroke-width=".8" fill="none"/></symbol>
    <symbol id="icon-web" viewBox="0 0 10 10"><circle cx="5" cy="5" r="4" fill="#e01b2b"/><path d="M1 5h8M5 1c-2 2.4-2 5.6 0 8M5 1c2 2.4 2 5.6 0 8" stroke="#fff" stroke-width=".6" fill="none"/></symbol>
    <symbol id="icon-pin" viewBox="0 0 10 10"><path d="M5 .8a3 3 0 0 1 3 3C8 6 5 9.2 5 9.2S2 6 2 3.8a3 3 0 0 1 3-3z" fill="#e01b2b"/><circle cx="5" cy="3.8" r="1.1" fill="#fff"/></symbol>
  </defs>
</svg>

<!-- Envelope front -->
<section class="piece envelope-front" aria-label="Envelope front">
  <div class="wordmark">Brennick</div>
  <div class="contact">
    <div>88 Ridgeway Ave. Suite 310</div>
    <div>Mississauga, ON L5T 2K1</div>
    <div class="gap"></div>
    <div class="contact-line"><svg class="icon" width="5" height="5"><use href="#icon-phone"/></svg>(416) 555-0184</div>
    <div class="contact-line"><svg class="icon" width="5" height="5"><use href="#icon-mail"/></svg>hello@brennicksupply.ca</div>
    <div class="contact-line"><svg class="icon" width="5" height="5"><use href="#icon-web"/></svg>www.brennicksupply.ca</div>
  </div>
  <div class="band"><span class="band-red"></span><span class="band-black"></span></div>
</section>

<!-- Envelope back -->
<section class="piece envelope-back" aria-label="Envelope back">
  <div class="flap"></div>
</section>

<!-- Business card front -->
<section class="piece card-front" aria-label="Business card front">
  <div class="wordmark">Brennick</div>
</section>

<!-- Business card back -->
<section class="piece contact-card" aria-label="Business card back">
  <div class="wordmark">Brennick</div>
  <div class="divider"></div>
  <div class="details contact">
    <div class="person-name"><span class="first">Mira</span> Castell</div>
    <div class="person-title">Founder &amp; CEO</div>
    <div class="block">88 Ridgeway Ave. Suite 310<br>Mississauga, ON L5T 2K1</div>
    <div class="contact-line"><svg class="icon" width="7" height="7"><use href="#icon-phone"/></svg>(416) 555-0184</div>
    <div class="contact-line"><svg class="icon" width="7" height="7"><use href="#icon-web"/></svg>hello@brennicksupply.ca</div>
    <div class="contact-line"><svg class="icon" width="7" height="7"><use href="#icon-mail"/></svg>www.brennicksupply.ca</div>
  </div>
  <div class="band"><span class="band-red"></span><span class="band-black"></span></div>
</section>

<!-- Letterhead -->
<section class="piece letterhead" aria-label="Letterhead">
  <div class="wordmark">Brennick</div>
  <div class="head-contact contact">
    <div class="contact-line">(416) 555-0184 <svg class="icon" width="6" height="6"><use href="#icon-phone"/></svg></div>
    <div class="contact-line">hello@brennicksupply.ca <svg class="icon" width="6" height="6"><use href="#icon-web"/></svg></div>
    <div class="contact-line">www.brennicksupply.ca <svg class="icon" width="6" height="6"><use href="#icon-mail"/></svg></div>
    <div class="gap"></div>
    <div class="contact-line">88 Ridgeway Ave. Suite 310 <svg class="icon" width="6" height="6"><use href="#icon-pin"/></svg></div>
    <div class="contact-line">Mississauga, ON L5T 2K1 <span style="width:6px;display:inline-block"></span></div>
  </div>
  <div class="rule-black"></div>
  <div class="rule-red"></div>

  <div class="letter-body">
    <div class="date">August-05-2019</div>
    <div class="recipient">Dana Whitlock</div>
    <div>Director</div>
    <div class="addr">88 Ridgeway Ave. Suite 310<br>Mississauga, ON L5T 2K1</div>
    <div class="salutation">Dana Whitlock</div>
    <p class="copy">Lorem ipsum dolor sit amet, consectetuer adipiscing elit, sed diam nonummy nibh euismod tincidunt ut laoreet dolore magna aliquam erat volutpat. Ut wisi enim ad minim veniam, quis nostrud exerci tation ullamcorper suscipit lobortis</p>
    <p class="copy">Lorem ipsum dolor sit amet, cons ectetuer adipiscing elit, sed diam nonummy nibh euismod tincidunt ut laoreet dolore magna aliquam erat volutpat. Ut wisi enim ad minim veniam, quis nostrud exerci tation ullamcorper suscipit lobortis nisl ut aliquip ex ea commodo consequat. Lorem ipsum dolor sit amet, consectetuer olutpat. Ut wisi enim ad minim veniam, quis nostrud exerci tation ullamcorper suscipit lobortis nisl ut aliquip ex ea commodo consequat. Duis autem</p>
    <p class="copy">vel eum iriure dolor in hendrerit in vulputate velit esse molestie consequat, vel illum dolore eu feugiat nulla facilisis at vero eros et accumsan et iusto odio dignissim qui blandit praesent luptatum zzril delenit augue duis dolore te feugait nulla facilisi. Lorem ipsum dolor sit amet, cons ectetuer adipiscing elit, sed diam nonummy nibh euismod tincidunt ut laoreet dolore magna aliquam erat volutpat. Ut wisi enim .</p>
  </div>

  <div class="signature" role="img" aria-label="Handwritten signature of Owen Hartley"></div>
  <div class="signer">
    <div class="name">Owen Hartley</div>
    <div class="role">Co-Founder</div>
  </div>
  <div class="band"><span class="band-red"></span><span class="band-black"></span></div>
</section>

<!-- Email signature -->
<section class="piece email-signature" aria-label="Email signature">
  <div class="wordmark">Brennick</div>
  <div class="divider"></div>
  <div class="details contact">
    <div class="person-name"><span class="first">Mira</span> Castell</div>
    <div class="person-title">Founder &amp; CEO</div>
    <div class="block">88 Ridgeway Ave. Suite 310<br>Mississauga, ON L5T 2K1</div>
    <div class="contact-line"><svg class="icon" width="6" height="6"><use href="#icon-phone"/></svg>(416) 555-0184</div>
    <div class="contact-line"><svg class="icon" width="6" height="6"><use href="#icon-web"/></svg>hello@brennicksupply.ca</div>
    <div class="contact-line"><svg class="icon" width="6" height="6"><use href="#icon-mail"/></svg>www.brennicksupply.ca</div>
  </div>
  <div class="band"><span class="band-red"></span><span class="band-black"></span></div>
</section>

<!-- Presentation folder -->
<section class="piece folder-front" aria-label="Presentation folder cover">
  <div class="wordmark">Brennick</div>
  <div class="band"><span class="band-red"></span><span class="band-black"></span></div>
</section>

<section class="piece folder-inside" aria-label="Presentation folder inside with pocket">
  <div class="pocket"></div>
</section>

<!-- Notepad cover -->
<section class="piece notepad" aria-label="Notepad cover">
  <div class="binding">
    <span class="ring"></span><span class="ring"></span><span class="ring"></span><span class="ring"></span><span class="ring"></span><span class="ring"></span><span class="ring"></span><span class="ring"></span><span class="ring"></span><span class="ring"></span><span class="ring"></span><span class="ring"></span><span class="ring"></span><span class="ring"></span><span class="ring"></span><span class="ring"></span><span class="ring"></span><span class="ring"></span><span class="ring"></span><span class="ring"></span>
  </div>
  <div class="wordmark">Brennick</div>
  <div class="band"><span class="band-red"></span><span class="band-black"></span></div>
</section>

</body>
</html>
```